Need App for Impact Related Events

My app is to help with internal events. When you enter the prompted event code the next screen shows you everyone currently at the event. It will give you the ability to Start a conversation with someone you met at that event, or signal it is your turn to send a message. The next screen is a message thread with that person. I am looking for a design that incorporates the colors and ‘feel good’ emotion of our logo. I have pieced together a pretty good interpretation of what I’m looking for in the attached mockup by slicing and dicing designs. I also attached our logo mascot.Screens (see attached mockups)

Note 1: I do not like the picture on the screen used in screen one because it makes it seem like a dating app. I attached an alternative photo that can be used or present different ideas.

Note 2: On the login/signup screen (screen 2) I need an additional first and last name for login, you can try to fit this on one login screen or present a two step signup screen where that is presented in the second screen.

READ MOCKUP GUIDELINES UNDER Must Haves

Target Market(s)

People attending internal social impact events

Industry/Entity Type

Charity

Font styles to use
Sans Serif

Colors
86cfc6

Requirements
Must have
• Follow the screen mockups attached to project
• PLEASE READ
• I have provided a relatively close design of what I’m looking for in the mockups. Some screens need to be followed more closely to my design mockup than other. I have listed a guide below how how closely you should follow my mockup design exactly. Overall I would like to see some ideas of incorporating a few accent colors so it doesn’t appear SO Blue. I also attached some app inspiration designs I found from around the web
• Screen Mockup Guideline Follow %
• Screen 1: 65% - mostly on target, would like to see ways to make it not SO Blue and possibly creative places to add some explainer text describing the app
• Screen 2: 50% - general design idea is here, but more open
• Screen 3: 35% - a lot more room for design influence
• Screen 4: 70% - mostly on target, a little room for design influence/color scheme ideas
• Screen 5-6: 25% - a lot of room for design change/ideas/influence
• Screen 7-8: 80% - already very close to what I need, maybe open to slight sizing and color scheme ideas
• Screen 9: 15% - the most open for influence, only the general functionality of the screen is communicated here
Nice to have
• Please Read Mockup Guideline above. In large part I am looking for something to use some nice accent colors so it is not overwhelmingly blue and bring the whole design into a seamless style.
Should not have

```html
<!DOCTYPE html>
<html lang="en">
<head>
<meta charset="utf-8">
<title>Create Event – Event Code</title>
<link rel="stylesheet" href="https://fonts.googleapis.com/css2?family=Nunito:wght@400;600;700;800&display=swap">
<style>
  :root {
    --bg-lilac: #c39ae9;
    --bg-rose: #e8c6e1;
    --title: #7b51b1;
    --field-border: rgba(255, 255, 255, 0.35);
    --field-fill: rgba(255, 255, 255, 0.08);
    --placeholder: #8a62bb;
    --scrim: rgba(255, 255, 255, 0.12);
    --card: #ffffff;
    --card-title: #1f1f24;
    --code: #9b52e3;
    --body-text: #56565e;
    --btn-start: #9a55e6;
    --btn-end: #dc92b6;
    --icon: #8a5bc4;
    --fab-start: #b77fdc;
    --fab-end: #d98ec2;
    --avatar: #a0806e;
    --white: #ffffff;
  }
  * { box-sizing: border-box; margin: 0; padding: 0; }
  html, body { width: 675px; height: 1200px; overflow: hidden; }
  body {
    font-family: "Nunito", sans-serif;
    background: linear-gradient(120deg, var(--bg-lilac) 0%, #d5aee6 55%, var(--bg-rose) 100%);
    position: relative;
  }
  .screen-title {
    position: absolute; left: 30px; top: 34px;
    font-size: 52px; font-weight: 800; color: var(--title); letter-spacing: 0.5px;
  }
  .avatar {
    position: absolute; left: 581px; top: 32px; width: 62px; height: 62px;
    border-radius: 50%; background: radial-gradient(circle at 45% 40%, #c9a690, var(--avatar) 70%);
    border: 2px solid rgba(255,255,255,0.5);
  }
  .field {
    position: absolute; left: 56px; width: 563px;
    border: 2px solid var(--field-border); background: var(--field-fill);
    border-radius: 6px; color: var(--placeholder); font-size: 27px;
    padding: 22px 0 0 28px;
  }
  .field-name { top: 141px; height: 75px; }
  .field-category { top: 234px; height: 75px; }
  .field-category svg { position: absolute; right: 26px; top: 26px; }
  .field-description { top: 332px; height: 287px; }
  .field-date { top: 660px; height: 56px; padding-top: 10px; }
  .scrim { position: absolute; inset: 0; background: var(--scrim); }
  .code-card {
    position: absolute; left: 88px; top: 302px; width: 501px; height: 596px;
    background: var(--card); border-radius: 8px;
    box-shadow: 0 6px 24px rgba(90, 50, 130, 0.18);
    text-align: center;
  }
  .code-card h2 {
    margin-top: 28px; font-size: 35px; font-weight: 600; color: var(--card-title);
  }
  .event-code {
    margin-top: 92px; font-size: 35px; font-weight: 700; color: var(--code); letter-spacing: 1.5px;
  }
  .code-hint {
    margin: 56px auto 0; width: 480px; font-size: 24px; line-height: 32px; color: var(--body-text);
    white-space: nowrap;
  }
  .btn-dismiss {
    position: absolute; left: 100px; top: 470px; width: 300px; height: 74px;
    border: none; border-radius: 6px;
    background: linear-gradient(90deg, var(--btn-start), var(--btn-end));
    color: var(--white); font-family: "Nunito", sans-serif; font-size: 22px; font-weight: 800;
    letter-spacing: 1.5px;
  }
  .tab-bar { position: absolute; left: 0; top: 1080px; width: 675px; height: 120px; }
  .tab-icon { position: absolute; top: 48px; }
  .tab-calendar { left: 42px; }
  .tab-chat { left: 181px; top: 50px; }
  .tab-bell { left: 451px; }
  .tab-filters { left: 583px; top: 50px; }
  .fab-close {
    position: absolute; left: 285px; top: 4px; width: 104px; height: 104px; border-radius: 50%;
    background: linear-gradient(135deg, var(--fab-start), var(--fab-end));
    display: flex; align-items: center; justify-content: center;
  }
</style>
</head>
<body>
  <h1 class="screen-title">Create Event</h1>
  <div class="avatar" role="img" aria-label="User profile photo"></div>

  <div class="field field-name">Event Name</div>
  <div class="field field-category">Catagory
    <svg width="34" height="20" viewBox="0 0 34 20"><path d="M2 2 L17 17 L32 2" fill="none" stroke="var(--icon)" stroke-width="3" stroke-linecap="round" stroke-linejoin="round"/></svg>
  </div>
  <div class="field field-description"></div>
  <div class="field field-date">T</div>

  <div class="scrim"></div>

  <section class="code-card">
    <h2>Your Event Code</h2>
    <p class="event-code">A34FVVG5</p>
    <p class="code-hint">Share this code with the people you<br>want to invite to this event.<br>Don’t forget to mention that they’ll<br>need "Kindly Together" app to enter<br>this code.</p>
    <button class="btn-dismiss">DISMISS</button>
  </section>

  <nav class="tab-bar">
    <svg class="tab-icon tab-calendar" width="50" height="50" viewBox="0 0 50 50">
      <rect x="3" y="7" width="44" height="40" rx="3" fill="none" stroke="var(--icon)" stroke-width="3.5"/>
      <line x1="3" y1="18" x2="47" y2="18" stroke="var(--icon)" stroke-width="3.5"/>
      <line x1="14" y1="2" x2="14" y2="11" stroke="var(--icon)" stroke-width="3.5" stroke-linecap="round"/>
      <line x1="36" y1="2" x2="36" y2="11" stroke="var(--icon)" stroke-width="3.5" stroke-linecap="round"/>
    </svg>
    <svg class="tab-icon tab-chat" width="46" height="46" viewBox="0 0 46 46">
      <path d="M23 5 A18 18 0 1 1 10 36 L5 41 L7 33 A18 18 0 0 1 23 5 Z" fill="none" stroke="var(--icon)" stroke-width="3.5" stroke-linejoin="round"/>
    </svg>
    <div class="fab-close">
      <svg width="34" height="34" viewBox="0 0 34 34"><path d="M4 4 L30 30 M30 4 L4 30" stroke="var(--white)" stroke-width="3" stroke-linecap="round"/></svg>
    </div>
    <svg class="tab-icon tab-bell" width="44" height="48" viewBox="0 0 44 48">
      <path d="M22 4 C12 4 9 12 9 20 L9 30 L4 37 L40 37 L35 30 L35 20 C35 12 32 4 22 4 Z" fill="none" stroke="var(--icon)" stroke-width="3.5" stroke-linejoin="round"/>
      <path d="M16 41 A6 6 0 0 0 28 41" fill="var(--icon)"/>
    </svg>
    <svg class="tab-icon tab-filters" width="50" height="46" viewBox="0 0 50 46">
      <line x1="3" y1="13" x2="47" y2="13" stroke="var(--icon)" stroke-width="3.5" stroke-linecap="round"/>
      <line x1="3" y1="33" x2="47" y2="33" stroke="var(--icon)" stroke-width="3.5" stroke-linecap="round"/>
      <circle cx="33" cy="13" r="6" fill="#d9b2e6" stroke="var(--icon)" stroke-width="3.5"/>
      <circle cx="17" cy="33" r="6" fill="#d9b2e6" stroke="var(--icon)" stroke-width="3.5"/>
    </svg>
  </nav>
</body>
</html>
```